Steel Rebar Fabrication Company needs Facebook Ads & page, Instagram Ads & pages designed.

I want to put out an Instagram, Facebook ad, and LinkedIn campaign out for my new company, Ridgeline Metals Inc. I want the ads to be short but clean, clear and precise. I want our address: 4871 Marrowfield Rd. Tsawwassen, BC. I want our hours of operation to be listed 8:00am to 4:00pm Monday to Friday. Product Delivery to your job site or pick up at our yard available. We can cut, bend to custom and standard shapes based upon Canadian CSA Standards. We offer products ranging from 10mm to 35mm diameter Grade 400W rebar. We can bend stirrups, dowels, hairpins; whatever your company needs to complete your product. Whether it is a small project, Tilt Up warehouse, Wood Frame Construction with Concrete parkade foundation; we have the team to meet your needs.
Email address: info@ridgelinemetalsinc.ca
We can service all areas of British Columbia.

Target Market(s)

Construction Company's for homes, condominiums, warehouses, commercial, industrial, and infrastructure projects. As well, as the every day DIY home improvement or renovator.

Industry/Entity Type

Construction

Requirements
Nice to have
• Would like to see a image of the rebar steel that I have provided in the ad. Even if it is in the background with a lower opacity level. Bonus if someone includes any of the movie files I have uploaded.

```html
<!DOCTYPE html>
<html lang="en">
<head>
<meta charset="utf-8">
<title>Ridgeline Metals Inc. – Hours of Operation Ad</title>
<link href="https://fonts.googleapis.com/css2?family=Russo+One&family=Montserrat:wght@600&family=Archivo:wght@800&display=swap" rel="stylesheet">
<style>
  :root {
    --bg-deep: #1c2c34;
    --bg-mid: #2f4852;
    --bg-light: #4b6670;
    --brand-red: #c8202f;
    --brand-red-dark: #9e1522;
    --ink-white: #ffffff;
    --ink-soft: #dfe6e9;
  }
  * { margin: 0; padding: 0; box-sizing: border-box; }
  html, body { width: 1200px; height: 675px; overflow: hidden; background: var(--bg-deep); }
  .ad {
    position: relative;
    width: 1200px;
    height: 675px;
    overflow: hidden;
    background: radial-gradient(ellipse at 38% 45%, var(--bg-light) 0%, var(--bg-mid) 40%, var(--bg-deep) 100%);
    color: var(--ink-white);
  }
  .brand {
    position: absolute;
    left: 120px;
    top: 62px;
    width: 400px;
    display: flex;
    align-items: center;
    gap: 16px;
  }
  .brand-mark {
    width: 54px; height: 54px;
    border-radius: 50%;
    background: var(--brand-red);
    flex: none;
  }
  .brand-name {
    font-family: "Montserrat", sans-serif;
    font-weight: 600;
    font-size: 34px;
    line-height: 1.1;
    color: var(--ink-white);
    letter-spacing: 1px;
  }
  .hero-art {
    position: absolute;
    left: 20px;
    top: 230px;
    width: 700px;
    height: 445px;
    background: radial-gradient(ellipse at 55% 55%, #c9d2d6 0%, #8ea0a7 30%, rgba(60,90,100,0.4) 60%, rgba(47,72,82,0) 78%);
  }
  .hours-banner {
    position: absolute;
    left: 760px;
    top: 46px;
    width: 440px;
    height: 62px;
    background: var(--brand-red);
    clip-path: polygon(16px 0, 100% 0, 100% 100%, 0 100%, 0 22px);
    padding: 6px 0 0 36px;
  }
  .hours-title {
    font-family: "Russo One", sans-serif;
    font-size: 30px;
    line-height: 1;
    letter-spacing: 0.5px;
  }
  .hours-time {
    font-family: "Russo One", sans-serif;
    font-size: 16px;
    line-height: 1.3;
    letter-spacing: 0.6px;
  }
  .service-copy {
    position: absolute;
    left: 798px;
    top: 128px;
    width: 390px;
    font-family: "Archivo", sans-serif;
    font-weight: 800;
    font-size: 15px;
    line-height: 20px;
    color: var(--ink-white);
  }
  .service-copy p + p { margin-top: 17px; }
  .contact-band {
    position: absolute;
    left: 760px;
    top: 642px;
    transform: translateY(-100%);
    width: 440px;
    height: 72px;
    background: linear-gradient(90deg, var(--brand-red) 0%, var(--brand-red) 70%, var(--brand-red-dark) 100%);
    clip-path: polygon(16px 0, 100% 0, 100% 100%, 0 100%, 0 22px);
    padding: 8px 0 0 38px;
    font-family: "Archivo", sans-serif;
    font-weight: 800;
    font-size: 14.5px;
    line-height: 20px;
  }
  .social {
    position: absolute;
    left: 340px;
    top: 670px;
    transform: translateY(-100%);
    padding-bottom: 28px;
  }
  .social-lead {
    font-family: "Montserrat", sans-serif;
    font-weight: 600;
    font-size: 8.5px;
    line-height: 11px;
    color: var(--ink-soft);
  }
  .social-lead strong { color: var(--ink-white); font-size: 9.5px; }
  .social-icons { display: flex; gap: 6px; margin-top: 6px; }
  .social-icons span {
    width: 18px; height: 18px;
    border-radius: 3px;
    background: var(--brand-red);
  }
</style>
</head>
<body>
  <main class="ad">
    <div class="hero-art" role="img" aria-label="Illustration of a gloved hand holding a silver tray carrying a city skyline on grass, clouds and a full moon"></div>

    <header class="brand">
      <span class="brand-mark"></span>
      <span class="brand-name">Ridgeline Metals Inc.</span>
    </header>

    <section class="hours-banner">
      <h1 class="hours-title">HOURS OF OPERATION</h1>
      <p class="hours-time">8:00AM TO 4:00PM MONDAY TO FRIDAY</p>
    </section>

    <section class="service-copy">
      <p>We can cut, bend to custom and standard<br>shapes based upon Canadian CSA Standards.<br>We offer products ranging from 10mm to<br>35mm diameter Grade 400W rebar. We can<br>bend stirrups, dowels, hairpins; whatever<br>your<br>company needs to complete your<br>product. Whether it is a small project, Tilt<br>Up warehouse, Wood Frame Construction<br>with Concrete<br>parkade foundation; we have the team to</p>
      <p>Construction Company's for homes,<br>condominiums, warehouses, commercial,<br>industrial, and infrastructure projects. As<br>well, as the every day DIY home<br>improvement or renovator.</p>
      <p>Product Delivery to your job site or pick up<br>at our yard available.</p>
    </section>

    <section class="contact-band">
      <p>Email address: info@ridgelinemetalsinc.ca</p>
      <p>4871 Marrowfield Rd. Tsawwassen, BC</p>
      <p>We can service all areas of British Columbia.</p>
    </section>

    <aside class="social">
      <p class="social-lead">JOIN US ON<br><strong>OUR SOCIAL MEDIA PLATFORM</strong></p>
      <div class="social-icons"><span></span><span></span><span></span></div>
    </aside>
  </main>
</body>
</html>
```